Business Card Design

I give lessons and clinics for dressage riders
I would like the design to be an outline (with broad lines) of a dressage horse and rider with in background of whole card with print over top tan or parchment card with burgundy print

Industry/Entity Type

Business

Contact Information for Business Card

Dale Ferrin
612-374-2059
Classical dressage training for the modern American
Clinics, lessons, training level -Prix St. George

Requirements
Must have
• broad lined outline of dressage horse and rider

```html
<!DOCTYPE html>
<html lang="en">
<head>
<meta charset="utf-8">
<title>Dale Ferrin — Business Card</title>
<link rel="stylesheet" href="https://fonts.googleapis.com/css2?family=Arimo:wght@400;700&display=swap">
<style>
  :root {
    --page-bg: #e9e6e1;
    --card-dark: #0b0b0b;
    --card-dark-edge: #1f1f1f;
    --art-tone-a: #4a4a4a;
    --art-tone-b: #2a2a2a;
    --card-parchment: #f1e6cc;
    --card-parchment-edge: #e6d6b3;
    --ink-burgundy: #6b1a26;
    --ink-burgundy-soft: #8a3a44;
  }
  * { box-sizing: border-box; margin: 0; padding: 0; }
  html, body {
    width: 1200px;
    height: 800px;
    overflow: hidden;
    background: var(--page-bg);
    font-family: "Arimo", Arial, sans-serif;
  }
  .canvas {
    width: 1200px;
    height: 800px;
    display: flex;
    align-items: center;
    justify-content: center;
    gap: 40px;
  }
  .card {
    width: 540px;
    height: 309px;
    border-radius: 4px;
    box-shadow: 0 6px 18px rgba(0,0,0,0.18);
    overflow: hidden;
    position: relative;
  }
  .card--back {
    background: linear-gradient(180deg, var(--card-dark-edge) 0%, var(--card-dark) 45%);
  }
  .card__art {
    position: absolute;
    left: 20px;
    top: 24px;
    width: 400px;
    height: 270px;
    display: block;
  }
  .card--front {
    background: linear-gradient(160deg, var(--card-parchment) 0%, var(--card-parchment-edge) 100%);
    text-align: center;
    color: var(--ink-burgundy);
  }
  .contact {
    position: absolute;
    top: 62px;
    left: 0;
    right: 0;
  }
  .contact__name {
    font-size: 25px;
    font-weight: 400;
    color: var(--ink-burgundy);
    letter-spacing: 0.2px;
  }
  .contact__phone {
    font-size: 14px;
    color: var(--ink-burgundy-soft);
    margin-top: 2px;
    letter-spacing: 0.5px;
  }
  .services {
    position: absolute;
    top: 158px;
    left: 0;
    right: 0;
    font-size: 15px;
    line-height: 1.15;
  }
  .services__tagline { margin-bottom: 12px; }
  .services__item { margin-bottom: 10px; }
</style>
</head>
<body>
  <main class="canvas">
    <section class="card card--back" aria-label="Card back">
      <svg class="card__art" viewBox="0 0 400 270" role="img" aria-label="Broad-lined outline illustration of a dressage horse and rider">
        <defs>
          <linearGradient id="artFill" x1="0" y1="0" x2="1" y2="1">
            <stop offset="0%" stop-color="var(--art-tone-a)"/>
            <stop offset="100%" stop-color="var(--art-tone-b)"/>
          </linearGradient>
        </defs>
        <rect x="0" y="0" width="400" height="270" rx="10" fill="url(#artFill)"/>
      </svg>
    </section>

    <section class="card card--front" aria-label="Card front">
      <div class="contact">
        <h1 class="contact__name">Dale Ferrin</h1>
        <p class="contact__phone">612-374-2059</p>
      </div>
      <div class="services">
        <p class="services__tagline">Classical dressage training for the<br>modern American Clinics</p>
        <p class="services__item">lessons</p>
        <p class="services__item">training level</p>
        <p class="services__item">Prix St. George</p>
      </div>
    </section>
  </main>
</body>
</html>
```